Construction company business card

One side to be the logo with the company name, The other side I would like: (Tomas verbick) Project manager 41 barrow crescent kelmore 52917306224783(03) 9703 2428Info@gudeljgroup.comAnd then maybe a couple dot points saying what we do:Construction (commercial & industrial) Civil construction

Anything else please contact me!
Maybe curved st one edge of the card

Target Market(s)

Older clientele

Industry/Entity Type

Construction Company

Contact Information for Business Card

Read above

Colors
3277b5
1b1b1b
9d9d9d

Requirements
Must have
• Use my logo on one side
Nice to have
• Read above
Should not have
• Read above

```html
<!DOCTYPE html>
<html lang="en">
<head>
<meta charset="utf-8">
<title>Hartwell Property Group – Business Card</title>
<link rel="stylesheet" href="https://fonts.googleapis.com/css2?family=Lato:wght@700&family=Open+Sans:wght@400;700&display=swap">
<style>
  :root {
    --backdrop: #e9e6e1;
    --kraft-light: #d3ad7e;
    --kraft-mid: #c19a6b;
    --kraft-dark: #a87b4f;
    --ink: #1b1b1b;
    --rule: #5a4632;
  }
  * { box-sizing: border-box; margin: 0; padding: 0; }
  html, body {
    width: 1200px; height: 900px; overflow: hidden;
    background: var(--backdrop);
  }
  .canvas { position: relative; width: 1200px; height: 900px; }
  .card {
    position: absolute;
    width: 556px; height: 343px;
    background: linear-gradient(160deg, var(--kraft-light) 0%, var(--kraft-mid) 45%, var(--kraft-dark) 100%);
    color: var(--ink);
    font-family: "Open Sans", Arial, sans-serif;
    text-align: center;
  }
  .card--front { left: 330px; top: 90px; }
  .card--back { left: 330px; top: 470px; width: 558px; }

  .person-name {
    position: absolute; left: 0; right: 0; top: 85px;
    font-family: "Lato", Arial, sans-serif; font-weight: 700;
    font-size: 21px; letter-spacing: 0.3px; line-height: 1;
  }
  .person-role {
    position: absolute; left: 0; right: 0; top: 106px;
    font-size: 15.5px; line-height: 1;
  }
  .icon-divider {
    position: absolute; left: 190px; top: 133px; width: 176px; height: 20px;
  }
  .contact-list {
    position: absolute; left: 0; right: 0; top: 161px;
    list-style: none; font-size: 16px; line-height: 20px;
  }
  .rule {
    position: absolute; height: 1px; background: var(--rule);
  }
  .rule--front { left: 190px; width: 176px; top: 233px; }
  .address {
    position: absolute; left: 0; right: 0; top: 243px;
    font-size: 16px; line-height: 20px; font-style: normal;
  }

  .brand {
    position: absolute; left: 0; right: 0; top: 58px;
    display: flex; flex-direction: column; align-items: center;
    font-family: "Open Sans", Arial, sans-serif; font-weight: 700;
    color: var(--ink);
  }
  .brand-mark {
    width: 118px; height: 118px; border-radius: 50%;
    background: var(--ink); margin-bottom: 20px;
  }
  .brand-name { font-size: 32px; line-height: 1; letter-spacing: 1px; }
  .brand-sub { font-size: 11px; letter-spacing: 5px; line-height: 1; margin-top: 4px; }
  .rule--back { left: 47px; width: 465px; top: 278px; }
  .services {
    position: absolute; left: 0; right: 0; top: 287px;
    list-style: none; font-size: 16px; line-height: 20px;
    display: flex; justify-content: center; gap: 6px;
  }
  .services li::before { content: "\25CF"; font-size: 12px; margin-right: 5px; vertical-align: 1px; }
</style>
</head>
<body>
<main class="canvas">
  <section class="card card--front">
    <h1 class="person-name">TOMAS VERBICK</h1>
    <p class="person-role">Project manager</p>
    <svg class="icon-divider" viewBox="0 0 176 20" aria-hidden="true">
      <line x1="0" y1="10" x2="56" y2="10" stroke="#5a4632" stroke-width="1"/>
      <line x1="120" y1="10" x2="176" y2="10" stroke="#5a4632" stroke-width="1"/>
      <circle cx="66" cy="10" r="9" fill="#1b1b1b"/>
      <path d="M61 13 q0-4 5-4 q5 0 5 4 z M62 8 h8 v1.5 h-8 z" fill="#c19a6b"/>
      <circle cx="87" cy="10" r="9" fill="#1b1b1b"/>
      <rect x="83.5" y="4.5" width="7" height="11" rx="1.2" fill="none" stroke="#c19a6b" stroke-width="1.4"/>
      <circle cx="108" cy="10" r="9" fill="#1b1b1b"/>
      <rect x="103" y="6.5" width="10" height="7" fill="none" stroke="#c19a6b" stroke-width="1.3"/>
      <path d="M103 6.5 l5 4 l5 -4" fill="none" stroke="#c19a6b" stroke-width="1.3"/>
    </svg>
    <ul class="contact-list">
      <li>7306224783</li>
      <li>(03) 9418 6573</li>
      <li>Info@verbickgroup.com</li>
    </ul>
    <div class="rule rule--front"></div>
    <address class="address">41 barrow crescent<br>kelmore 5291</address>
  </section>

  <section class="card card--back">
    <div class="brand">
      <div class="brand-mark"></div>
      <span class="brand-name">HARTWELL</span>
      <span class="brand-sub">PROPERTY GROUP</span>
    </div>
    <div class="rule rule--back"></div>
    <ul class="services">
      <li>Construction (commercial &amp; industrial)</li>
      <li>Civil construction</li>
    </ul>
  </section>
</main>
</body>
</html>
```